Vortel surface design based website for technology jobs website

We need a website design for a technology job listing website, mainly aiming at 20/30/40 year old nerds. Jobs listed from multiple sources will be concatenated and organised. This website will be built with Vortel surface design (https://surfacekit.example/guidelines/) so please use their components. The design should be simple and clear, so a user can directly look for offerings that are interesting for him.

Three different pages will be needed:

1. Main jobs list page

Contains a large table (https://surfacekit.example/guidelines/components/data-tables.html#data-tables-structure), on top or next to this data-table users should be able to apply filters (select countries, select salary ranges) and somewhere an overview of the selected filters should be shown.

- A subscribe bar should be shown somewhere to allow a user to register for weekly/monthly mailings for new job offers with his preferred search filters.

2. Selected item page

If an item is clicked, a user should be able to view a job posting and it's details.

3. An advertiser should be able post his job offer.
Similar fields as https://post.ledgerworkboard.example/.
(https://surfacekit.example/guidelines/components/text-fields.html#text-fields-layout)

Target Market(s)

20/30/40 year old nerds.

Industry/Entity Type

Computer

Logo Text

TechHirePlaza.example

Number of Pages Required

3 page

Colors

Designer to choose colors to be used in the design.

Requirements
Must have
• 1. Main jobs list page
• Contains a large table (https://surfacekit.example/guidelines/components/data-tables.html#data-tables-structure), on top or next to this data-table users should be able to apply filters (select countries, select salary ranges) and somewhere an overview of the selected filters should be shown.
• - A subscribe bar should be shown somewhere to allow a user to register for weekly/monthly mailings for new job offers with his preferred search filters.
• 2. Selected item page
• If an item is clicked, a user should be able to view a job posting and it's details.
• 3. An advertiser should be able post his job offer,
• (https://surfacekit.example/guidelines/components/text-fields.html#text-fields-layout)
• Please use open fonts!

```html
<!DOCTYPE html>
<html lang="en">
<head>
<meta charset="utf-8">
<title>TechHirePlaza.example – Jobs</title>
<link href="https://fonts.googleapis.com/css2?family=Roboto:wght@400;500;700&display=swap" rel="stylesheet">
<style>
  :root{
    --hero-dark:#04101f;
    --hero-mid:#0b2a4a;
    --hero-glow:#1466a8;
    --band-blue:#03a0e8;
    --button-blue:#0d4f94;
    --page-grey:#ececec;
    --card-white:#ffffff;
    --row-stripe:#f4f4f4;
    --rule:#e3e3e3;
    --text-dark:#333333;
    --text-muted:#777777;
    --placeholder:#9a9a9a;
    --menu-teal:#1a9fb9;
    --drawer-grey-1:#8a8a8a;
    --drawer-grey-2:#3c3c3c;
    --accent-yellow:#e6dc1e;
  }
  *{box-sizing:border-box;margin:0;padding:0}
  html,body{width:1200px;height:590px;overflow:hidden}
  body{font-family:"Roboto",Arial,sans-serif;background:var(--page-grey);position:relative}

  .hero{position:absolute;left:0;top:0;width:1200px;height:397px;
    background:radial-gradient(ellipse at 35% 45%,var(--hero-glow) 0%,var(--hero-mid) 35%,var(--hero-dark) 80%);}
  .hero-title{position:absolute;top:18px;left:0;width:1200px;text-align:center;
    color:#fff;font-weight:700;font-size:30px;letter-spacing:.2px}

  .search-band{position:absolute;left:88px;top:105px;width:1025px;height:98px;background:var(--band-blue)}
  .field{position:absolute;top:28px;height:41px;background:#fff;border-radius:3px;
    font-size:12px;color:var(--placeholder);line-height:41px;padding-left:8px;white-space:nowrap;overflow:hidden}
  .field svg{position:absolute;right:8px;top:16px}
  .field-keywords{left:20px;width:299px;padding-left:14px}
  .field-location{left:328px;width:214px}
  .field-salary{left:551px;width:214px}
  .field-designation{left:773px;width:114px}
  .search-button{position:absolute;left:895px;top:28px;width:100px;height:41px;background:var(--button-blue);border-radius:3px}
  .search-button svg{position:absolute;left:40px;top:11px}

  .jobs-card{position:absolute;left:88px;top:267px;width:1025px;height:323px;background:var(--card-white)}
  .jobs-table{position:absolute;left:0;top:0;width:100%;border-collapse:collapse;font-size:12px}
  .jobs-table th{height:80px;padding-top:34px;text-align:left;font-weight:400;color:var(--text-dark);
    border-bottom:1px solid var(--rule);vertical-align:top}
  .jobs-table td{height:50px;color:var(--text-dark);border-bottom:1px solid #f0f0f0}
  .jobs-table td.muted{color:var(--text-muted)}
  .jobs-table tr.stripe td{background:var(--row-stripe)}
  .col-title{width:239px}
  .col-country{width:185px}
  .col-exp{width:162px}
  .col-salary{width:137px}
  .col-skills{width:150px}
  .skills svg{margin-left:3px;vertical-align:middle}

  .drawer{position:absolute;left:0;top:0;width:219px;height:590px;background:#fff;box-shadow:2px 0 6px rgba(0,0,0,.25)}
  .drawer-head{position:absolute;left:0;top:0;width:219px;height:165px;overflow:hidden;
    background:linear-gradient(135deg,var(--drawer-grey-1) 0%,#6a6a6a 40%,var(--drawer-grey-2) 100%)}
  .drawer-corner{position:absolute;left:0;top:0}
  .drawer-brand{position:absolute;left:8px;top:66px;color:#fff;font-weight:700;font-size:18px}
  .drawer-close{position:absolute;left:183px;top:5px}
  .drawer-tab{position:absolute;left:212px;top:110px}
  .menu{list-style:none;position:absolute;left:0;top:165px;width:219px}
  .menu li{position:absolute;left:15px;height:20px;display:flex;align-items:center;
    color:var(--menu-teal);font-size:15px}
  .menu li svg{width:18px;height:16px;margin-right:10px}
</style>
</head>
<body>

<section class="hero" role="img" aria-label="Dark blue network-of-lines technology backdrop">
  <h1 class="hero-title">TechHirePlaza.example</h1>
</section>

<form class="search-band">
  <div class="field field-keywords">Keywords (Title, Description,Tags)
    <svg width="10" height="8" viewBox="0 0 10 8"><path d="M1 2l4 4 4-4" fill="none" stroke="#888" stroke-width="1.3"/></svg></div>
  <div class="field field-location">Select Location
    <svg width="10" height="8" viewBox="0 0 10 8"><path d="M1 2l4 4 4-4" fill="none" stroke="#888" stroke-width="1.3"/></svg></div>
  <div class="field field-salary">Salary
    <svg width="10" height="8" viewBox="0 0 10 8"><path d="M1 2l4 4 4-4" fill="none" stroke="#888" stroke-width="1.3"/></svg></div>
  <div class="field field-designation">Designation
    <svg width="10" height="8" viewBox="0 0 10 8"><path d="M1 2l4 4 4-4" fill="none" stroke="#888" stroke-width="1.3"/></svg></div>
  <div class="search-button">
    <svg width="20" height="20" viewBox="0 0 20 20"><circle cx="8" cy="8" r="6" fill="none" stroke="#fff" stroke-width="3"/><path d="M12.5 12.5l5.5 5.5" stroke="#fff" stroke-width="3.4" stroke-linecap="round"/></svg>
  </div>
</form>

<section class="jobs-card">
  <table class="jobs-table">
    <thead>
      <tr><th class="col-title">Job Title</th><th class="col-country">Country Name</th><th class="col-exp">Experience</th><th class="col-salary">Salary</th><th class="col-skills">Keyskills</th><th>Employment Type</th></tr>
    </thead>
    <tbody>
      <tr><td>Job Title</td><td>Country</td><td>0 -1</td><td class="muted">$ 20000</td><td class="muted skills">HTML Javascript<svg width="8" height="6" viewBox="0 0 8 6"><path d="M1 1l3 3 3-3" fill="none" stroke="#888" stroke-width="1.2"/></svg></td><td class="muted">Full Time</td></tr>
      <tr class="stripe"><td>Job Title</td><td>Country</td><td>0 -1</td><td class="muted">$ 20000</td><td class="muted skills">HTML Javascript<svg width="8" height="6" viewBox="0 0 8 6"><path d="M1 1l3 3 3-3" fill="none" stroke="#888" stroke-width="1.2"/></svg></td><td class="muted">Full Time</td></tr>
      <tr><td>Job Title</td><td>Country</td><td>0 -1</td><td class="muted">$ 20000</td><td class="muted skills">HTML Javascript<svg width="8" height="6" viewBox="0 0 8 6"><path d="M1 1l3 3 3-3" fill="none" stroke="#888" stroke-width="1.2"/></svg></td><td class="muted">Full Time</td></tr>
      <tr><td>Job Title</td><td>Country</td><td>0 -1</td><td class="muted">$ 20000</td><td class="muted skills">HTML Javascript<svg width="8" height="6" viewBox="0 0 8 6"><path d="M1 1l3 3 3-3" fill="none" stroke="#888" stroke-width="1.2"/></svg></td><td class="muted">Full Time</td></tr>
      <tr><td>Job Title</td><td>Country</td><td>0 -1</td><td class="muted">$ 20000</td><td class="muted skills">HTML Javascript<svg width="8" height="6" viewBox="0 0 8 6"><path d="M1 1l3 3 3-3" fill="none" stroke="#888" stroke-width="1.2"/></svg></td><td class="muted">Full Time</td></tr>
    </tbody>
  </table>
</section>

<nav class="drawer">
  <div class="drawer-head" role="img" aria-label="Grey angled-panel header backdrop">
    <svg class="drawer-corner" width="36" height="36" viewBox="0 0 36 36"><path d="M0 0h36L0 36z" fill="var(--accent-yellow)"/></svg>
    <span class="drawer-brand">TechHirePlaza.example</span>
    <svg class="drawer-close" width="28" height="28" viewBox="0 0 28 28"><circle cx="14" cy="14" r="12.5" fill="none" stroke="#fff" stroke-width="1.5"/><path d="M9 9l10 10M19 9L9 19" stroke="#fff" stroke-width="1.5"/></svg>
  </div>
  <svg class="drawer-tab" width="7" height="14" viewBox="0 0 7 14"><path d="M7 0v14L0 7z" fill="var(--accent-yellow)"/></svg>
  <ul class="menu">
    <li style="top:46px"><svg viewBox="0 0 18 16"><path d="M9 1L1 8h2.5v7h4v-5h3v5h4V8H17z" fill="var(--menu-teal)"/></svg>Home</li>
    <li style="top:102px"><svg viewBox="0 0 18 16"><path d="M1 1v14h16" fill="none" stroke="var(--menu-teal)" stroke-width="1.6"/><path d="M4 9h2v5H4zM7.5 5h2v9h-2zM11 7h2v7h-2zM14.5 3h2v11h-2z" fill="var(--menu-teal)"/></svg>Menu 1</li>
    <li style="top:160px"><svg viewBox="0 0 18 16"><circle cx="6" cy="4.5" r="3.5" fill="var(--menu-teal)"/><path d="M0 15c0-4 2.5-6 6-6s6 2 6 6z" fill="var(--menu-teal)"/></svg>Menu 2</li>
    <li style="top:217px"><svg viewBox="0 0 18 16"><path d="M12 3H2v12h12V8" fill="none" stroke="var(--menu-teal)" stroke-width="1.6"/><path d="M15 1l2 2-8 8H7V9z" fill="var(--menu-teal)"/></svg>Menu 3</li>
    <li style="top:274px"><svg viewBox="0 0 18 16"><path d="M2 1h11l3 3v11H2z" fill="none" stroke="var(--menu-teal)" stroke-width="1.6"/><path d="M5 2h6v4H5zM5 10h8v4H5z" fill="var(--menu-teal)"/></svg>Menu 4</li>
    <li style="top:331px"><svg viewBox="0 0 18 16"><path d="M3 7V5a3 3 0 0 1 6 0v2" fill="none" stroke="var(--menu-teal)" stroke-width="1.8"/><rect x="1" y="7" width="10" height="8" rx="1" fill="var(--menu-teal)"/></svg>Menu 5</li>
  </ul>
</nav>

</body>
</html>
```